Business Card Design Project

I need business cards communicate a high end look and cutting edge sophistication,creativity, with a logo branding.
The company name is: Sterling Craftworks we specialize in Remodel ing and Design of Resindental and Commercial our company is based in Los Angeles Ca our clients are high end high dollar . The design should communicate the statements above.
Updates
I would like to see both side the business card
Industry/Entity Type
Business
Requirements
Nice to have
- Maybe a design with a faint Blueprint /construction floor plan background, maybe

```html
<!DOCTYPE html>
<html lang="en">
<head>
<meta charset="utf-8">
<title>Sterling Craftworks – Business Card</title>
<link rel="stylesheet" href="https://fonts.googleapis.com/css2?family=Mulish:wght@300;400;700;800&display=swap">
<style>
  :root {
    --stage: #e9e7e3;
    --card-blue: #1f5cb5;
    --card-blue-deep: #17479a;
    --grid-line: rgba(255, 255, 255, 0.07);
    --paper: #f1f3f6;
    --paper-shade: #d9dde3;
    --ink-blue: #1e5bb3;
    --band-dark: #2b2e33;
    --white: #ffffff;
    --shadow: rgba(0, 0, 0, 0.22);
  }
  * { box-sizing: border-box; margin: 0; padding: 0; }
  html, body {
    width: 1200px;
    height: 880px;
    overflow: hidden;
    background: var(--stage);
    font-family: "Mulish", "Helvetica Neue", Arial, sans-serif;
  }
  .stage {
    width: 1200px;
    height: 880px;
    display: flex;
    flex-direction: column;
    align-items: center;
    justify-content: center;
    gap: 56px;
  }
  .card {
    position: relative;
    width: 620px;
    height: 354px;
    overflow: hidden;
    background:
      linear-gradient(var(--grid-line) 1px, transparent 1px) 0 0 / 24px 24px,
      linear-gradient(90deg, var(--grid-line) 1px, transparent 1px) 0 0 / 24px 24px,
      radial-gradient(ellipse at 40% 40%, var(--card-blue) 0%, var(--card-blue-deep) 100%);
    box-shadow: 0 10px 26px var(--shadow);
  }

  /* Front */
  .brand {
    position: absolute;
    left: 60px;
    top: 70px;
    width: 500px;
    color: var(--white);
    font-weight: 800;
    line-height: 0.95;
    text-align: right;
  }
  .brand-name-top {
    display: block;
    font-size: 74px;
    letter-spacing: 2px;
    text-transform: uppercase;
    text-align: left;
  }
  .brand-name-bottom {
    display: block;
    font-size: 50px;
    margin-top: 8px;
    margin-right: 6px;
  }
  .tagline-band {
    position: absolute;
    left: 0;
    right: 0;
    bottom: 22px;
    height: 42px;
    background: linear-gradient(180deg, var(--paper) 0%, var(--paper-shade) 100%);
    display: flex;
    align-items: center;
    justify-content: center;
  }
  .tagline {
    color: var(--ink-blue);
    font-size: 17px;
    font-weight: 400;
    letter-spacing: 7px;
    text-transform: uppercase;
  }

  /* Back */
  .name-band {
    position: absolute;
    top: 34px;
    left: 88px;
    right: 0;
    height: 46px;
    background: linear-gradient(180deg, var(--paper) 0%, var(--paper-shade) 100%);
    clip-path: polygon(22px 0, 100% 0, 100% 100%, 0 100%);
    display: flex;
    align-items: center;
    padding-left: 30px;
  }
  .person-name {
    color: var(--ink-blue);
    font-size: 30px;
    font-weight: 800;
    letter-spacing: 0.5px;
  }
  .contact-band {
    position: absolute;
    top: 80px;
    left: 78px;
    right: 0;
    height: 32px;
    background: var(--band-dark);
    clip-path: polygon(10px 0, 100% 0, 100% 100%, 0 100%);
    display: flex;
    align-items: center;
    padding-left: 36px;
    color: var(--white);
    font-size: 15px;
    font-weight: 400;
    letter-spacing: 0.3px;
  }
  .contact-divider { margin: 0 10px; opacity: 0.8; }
  .address {
    position: absolute;
    left: 34px;
    top: 140px;
    color: var(--white);
    font-size: 18px;
    font-weight: 300;
    font-style: normal;
    line-height: 1.4;
  }
  .license {
    display: block;
    margin-top: 4px;
    font-size: 10px;
    font-weight: 400;
  }
  .elevation-drawing {
    position: absolute;
    left: 270px;
    top: 124px;
    width: 330px;
    height: 222px;
    background: linear-gradient(160deg, rgba(255, 255, 255, 0.16) 0%, rgba(255, 255, 255, 0.05) 100%);
  }
</style>
</head>
<body>
  <main class="stage">
    <section class="card card-front" aria-label="Business card front">
      <h1 class="brand">
        <span class="brand-name-top">Sterling</span>
        <span class="brand-name-bottom">Craftworks</span>
      </h1>
      <div class="tagline-band">
        <p class="tagline">Remodeling &amp; Design</p>
      </div>
    </section>

    <section class="card card-back" aria-label="Business card back">
      <div class="name-band">
        <h2 class="person-name">Marcus Delaney</h2>
      </div>
      <div class="contact-band">
        <span class="contact-phone">323-555-0148</span>
        <span class="contact-divider">|</span>
        <span class="contact-email">marcus@sterlingcraftworks.net</span>
      </div>
      <address class="address">
        4821 Larchmont Ave<br>
        Suite# 210<br>
        Los Angeles, CA 90019
        <span class="license">License 570316</span>
      </address>
      <div class="elevation-drawing" role="img" aria-label="Line-drawn architectural elevation of a two-storey house with arched doorway, windows and balcony"></div>
    </section>
  </main>
</body>
</html>
```